Zielgruppe
Beamer Vermietung
Aufgabenstellung
Erstellung 2 professionell aussehender Webseiten.
Projektor-Verleih-Raum-Ostlingen.de
sowie
Projektor-Verleih-Raum-Wendbergshof.de
Die Seiten sind aktuell im Betrieb, aber haben ein sehr veraltetes Design.
Die Seiten können ähnlich aussehen, sollten aber etwas unterschiedlich sein, damit sie für den Kunden leicht anders aussehen.
Wichtig ist, dass alle Seiten, inklusive Startseite, Unterseiten und Links designed werden und das dieses Design in die bestehende Wordpress Installation eingepflegt wird.
Es ist also notwendig, gute Wordpress Kenntnisse zu haben um dann auch zwei fertige Wordpress Seiten liefern zu können.

```html
<!DOCTYPE html>
<html lang="de">
<head>
<meta charset="utf-8">
<title>Projektor-Verleih-Raum-Wendbergshof.de – Beamer mieten</title>
<link rel="stylesheet" href="https://fonts.googleapis.com/css2?family=Jost:wght@300;400;500;600&display=swap">
<style>
:root{
  --purple:#7a44b6;
  --purple-light:#9d5fcb;
  --purple-dark:#5e2f9c;
  --lavender:#ede4f6;
  --night:#2d1a52;
  --ink:#262329;
  --white:#ffffff;
}
*{box-sizing:border-box;margin:0;padding:0}
html,body{width:715px;height:1200px;overflow:hidden;background:var(--white)}
body{font-family:"Jost",sans-serif;color:var(--ink)}
.canvas{position:relative;width:715px;height:1200px;overflow:hidden}
.decor{position:absolute;left:0;top:0;width:715px;height:1200px}
.abs{position:absolute}

/* header */
.site-header{position:absolute;left:0;top:0;width:715px;height:37px;background:var(--white);border-bottom:1px solid #ddd3ea;z-index:3}
.brand{position:absolute;left:59px;top:9px;display:flex;align-items:center;gap:4px}
.brand-dot{width:19px;height:19px;border-radius:50%;background:var(--purple)}
.brand-name{font-size:7.5px;line-height:8.5px;font-weight:400;color:var(--purple)}
.main-nav{position:absolute;top:15px;left:0;width:715px;font-size:6.6px;font-weight:400;text-transform:uppercase}
.main-nav a{position:absolute;color:var(--ink);text-decoration:none;white-space:nowrap}
.main-nav a.active{color:var(--purple);font-weight:500;letter-spacing:.4px}
.main-nav a.active::before{content:"";position:absolute;left:0;right:0;top:-15px;height:1.5px;background:var(--purple)}

.photo{position:absolute}

/* hero */
.hero-title{left:109px;top:126px;font-size:12px;line-height:14.5px;font-weight:500;color:var(--ink)}
.hero-rule{left:109px;top:160px;width:49px;height:1px;background:var(--purple)}
.hero-sub{left:109px;top:172px;font-size:9px;font-weight:500}
.hero-lead{left:109px;top:188px;width:220px;font-size:8.7px;line-height:10.5px;font-weight:300}

.btn{position:absolute;height:18.5px;width:96px;border-radius:10px;display:flex;align-items:center;justify-content:space-between;padding:0 9px;font-size:4.8px;font-weight:500;letter-spacing:.4px;text-transform:uppercase;text-decoration:none}
.btn-solid{background:linear-gradient(90deg,var(--purple-dark),var(--purple-light));color:var(--white)}
.btn-ghost{border:1px solid var(--purple);color:var(--purple);background:var(--white)}
.btn svg{width:12px;height:4px}

.scroll-down{left:348px;top:282px;width:19px;height:19px;border-radius:50%;background:var(--purple);box-shadow:0 1px 3px rgba(0,0,0,.2);display:flex;align-items:center;justify-content:center}

.block-title{font-size:8px;line-height:11px;font-weight:500}
.copy{font-size:5.8px;line-height:7.5px;font-weight:300;color:var(--ink)}
.copy p+p{margin-top:7.5px}
.copy a{color:var(--purple);text-decoration:none}

/* feature cards */
.card{position:absolute;top:770px;width:153px;height:153px;border-radius:4px;overflow:hidden;background:linear-gradient(160deg,var(--purple-light),var(--purple))}
.card-visual{position:absolute;inset:0}
.card-icon{position:absolute;left:10px;top:9px;width:29px;height:22px}
.card-title{position:absolute;left:10px;top:35px;font-size:6.2px;font-weight:500;color:var(--white)}
.card-text{position:absolute;left:10px;top:121px;width:136px;font-size:5.8px;line-height:7.4px;font-weight:300;color:var(--white)}

/* contact */
.contact-art{left:123px;top:977px;width:158px;height:64px;background:linear-gradient(135deg,#f1eaf8,#e3d5f1);clip-path:polygon(0 100%,33% 8%,50% 0,100% 92%)}
.contact-kicker{left:399px;top:983px;font-size:6px;font-weight:500}
.contact-title{left:399px;top:995px;font-size:8px;font-weight:500}
.contact-lead{left:399px;top:1017px;width:210px;font-size:5.7px;line-height:7px;font-weight:300}
.contact-list{left:399px;top:1038px;list-style:none;font-size:6.3px;line-height:10.8px;font-weight:300}
.contact-list li{display:flex;align-items:center;gap:4px}
.contact-list li.company{color:var(--purple);font-weight:500}
.contact-list svg{width:5px;height:6px}

/* footer */
.footer-rule{left:109px;top:1163px;width:497px;height:1px;background:#6d5a92}
.footer-copy{left:112px;top:1173px;font-size:5.8px;font-weight:300;color:#e6ddf3}
.footer-links{left:517px;top:1173px;display:flex;align-items:center;gap:6px;font-size:5.8px;font-weight:300;color:#e6ddf3}
.footer-links .dot{width:6px;height:6px;border-radius:50%;border:.8px solid #e6ddf3}
</style>
</head>
<body>
<div class="canvas">

  <svg class="decor" viewBox="0 0 715 1200" aria-hidden="true">
    <defs>
      <linearGradient id="heroBg" x1="0" y1="0" x2="1" y2="0">
        <stop offset="0" stop-color="#8a4fbf"/>
        <stop offset="1" stop-color="#5a2f95"/>
      </linearGradient>
      <linearGradient id="heroLight" x1="0" y1="0" x2="1" y2="1">
        <stop offset="0" stop-color="#e6e5ea"/>
        <stop offset=".6" stop-color="#f6f6f8"/>
        <stop offset="1" stop-color="#ffffff"/>
      </linearGradient>
      <linearGradient id="band" x1="0" y1="0" x2="1" y2="0">
        <stop offset="0" stop-color="#9b5bcb"/>
        <stop offset="1" stop-color="#6c38ab"/>
      </linearGradient>
      <linearGradient id="bandRev" x1="1" y1="0" x2="0" y2="0">
        <stop offset="0" stop-color="#9b5bcb"/>
        <stop offset="1" stop-color="#6c38ab"/>
      </linearGradient>
    </defs>
    <rect x="0" y="37" width="715" height="254" fill="url(#heroBg)"/>
    <polygon points="0,51 414,113 511,188 562,291 0,291" fill="url(#heroLight)"/>
    <polygon points="0,306 308,436 0,505" fill="var(--lavender)"/>
    <polygon points="0,328 300,436 0,479" fill="url(#band)"/>
    <polygon points="715,513 460,578 401,646 715,748" fill="var(--lavender)"/>
    <path d="M715,542 L500,572 Q470,576 440,598 L404,624 Q396,640 414,644 L715,728 Z" fill="url(#bandRev)"/>
    <rect x="0" y="1092" width="715" height="108" fill="var(--night)"/>
  </svg>

  <header class="site-header">
    <div class="brand">
      <span class="brand-dot"></span>
      <span class="brand-name">Projektor-Verleih<br>Raum-Wendbergshof</span>
    </div>
    <nav class="main-nav">
      <a class="active" style="left:506px">Home</a>
      <a style="left:539px">Beamer mieten</a>
      <a style="left:598px">Preise</a>
      <a style="left:628px">Kontakt</a>
    </nav>
  </header>

  <div class="photo" role="img" aria-label="Weißer Heimkino-Projektor, schräg von vorne" style="left:362px;top:99px;width:185px;height:100px;border-radius:40px 20px 30px 50px;background:linear-gradient(160deg,#ffffff,#d9d9de);box-shadow:0 4px 8px rgba(0,0,0,.12)"></div>
  <h1 class="abs hero-title">Herzlich Willkommen bei<br>Projektor-Verleih-Raum-Wendbergshof.de</h1>
  <div class="abs hero-rule"></div>
  <h2 class="abs hero-sub">Beamer mieten zu TOP-Konditionen!</h2>
  <p class="abs hero-lead">Sie möchten einen Beamer im Raum Wendbergshof oder Umgebung mieten?</p>
  <a class="btn btn-solid" style="left:109px;top:222px">Beamer mieten<svg viewBox="0 0 12 4"><path d="M0 2H11M9 .5L11 2 9 3.5" stroke="#fff" stroke-width=".6" fill="none"/></svg></a>
  <a class="btn btn-ghost" style="left:218px;top:222px">Kontakt aufnehmen<svg viewBox="0 0 12 4"><path d="M0 2H11M9 .5L11 2 9 3.5" stroke="#7a44b6" stroke-width=".6" fill="none"/></svg></a>
  <div class="abs scroll-down"><svg width="7" height="5" viewBox="0 0 7 5"><path d="M1 1L3.5 3.5 6 1" stroke="#fff" stroke-width="1" fill="none"/></svg></div>

  <div class="photo" role="img" aria-label="Silberner Business-Projektor, seitlich" style="left:108px;top:377px;width:195px;height:90px;border-radius:6px 14px 30px 8px;background:linear-gradient(180deg,#f4f4f6,#c9c9cf);box-shadow:0 4px 8px rgba(0,0,0,.15)"></div>
  <h2 class="abs block-title" style="left:344px;top:352px;width:275px">Projektor-Verleih-Raum-Wendbergshof.de – Ihre Adresse für Projektor-Vermietung und Leinwand Anmietung!</h2>
  <div class="abs copy" style="left:344px;top:386px;width:265px">
    <p>Zu unseren Miet-Geräten können optional auch passende Leinwände zu Ihrem gewünschten Projektor hinzugebucht werden.<br>Unsere Projektoren und Leinwände gibt es bereits ab günstigen 30€ pro Tag. Alle Preise können Sie unserer Preisliste entnehmen.</p>
    <p>Unser Sortiment erstreckt sich von Heim-Projektoren für den privaten Bedarf über HD-fähige Geräte bis hin zu Business Full-HD-Geräten, die für großräumige Geschäftspräsentationen sowie für Full-HD TV Übertragungen geeignet sind. Somit haben Sie das perfekte Klang- und Bilderlebnis für Ihre Präsentation oder Ihr Event.</p>
  </div>
  <a class="btn btn-solid" style="left:344px;top:472px">Beamer mieten<svg viewBox="0 0 12 4"><path d="M0 2H11M9 .5L11 2 9 3.5" stroke="#fff" stroke-width=".6" fill="none"/></svg></a>

  <div class="abs copy" style="left:109px;top:582px;width:262px">
    <p>Wir bieten Ihnen die Möglichkeit, auch über Wochenenden zu vergünstigten Wochenend-Tarifen zu bestellen. Falls Sie Fragen zu dem Ablauf, zu den Projektoren oder zu dem Mietvorgang haben, können Sie uns jederzeit kontaktieren, wir helfen Ihnen gerne weiter!</p>
    <p>Sie kommen aus dem Raum Ostlingen? Unsere aktuellen Angebote hierfür finden Sie unter:<br><a>https://www.projektor-verleih-raum-ostlingen.de</a></p>
    <p>Bei Fragen zur Anfahrt können Sie unseren Anfahrt-Navigator unter <a>Kontakt</a> nutzen.</p>
  </div>
  <a class="btn btn-solid" style="left:109px;top:660px">Kontakt aufnehmen<svg viewBox="0 0 12 4"><path d="M0 2H11M9 .5L11 2 9 3.5" stroke="#fff" stroke-width=".6" fill="none"/></svg></a>
  <div class="photo" role="img" aria-label="Drei Projektoren aus dem Mietsortiment" style="left:398px;top:552px;width:210px;height:136px">
    <div class="abs" style="left:113px;top:0;width:97px;height:52px;border-radius:22px 10px 14px 22px;background:linear-gradient(160deg,#fff,#d4d4d9)"></div>
    <div class="abs" style="left:0;top:28px;width:95px;height:56px;border-radius:10px 16px 14px 14px;background:linear-gradient(160deg,#4a4a50,#15151a)"></div>
    <div class="abs" style="left:72px;top:84px;width:110px;height:52px;border-radius:6px 10px 22px 6px;background:linear-gradient(180deg,#f6f6f8,#c9c9cf)"></div>
  </div>

  <article class="card" style="left:109px">
    <div class="card-visual" role="img" aria-label="Nahaufnahme eines Projektorobjektivs" style="clip-path:polygon(88px 0,153px 0,153px 115px,62px 100px,50px 90px);background:linear-gradient(150deg,#6a6a70,#1d1d22)"></div>
    <svg class="card-icon" viewBox="0 0 29 22" fill="none" stroke="#fff" stroke-width=".9"><rect x="1" y="5" width="27" height="12" rx="2"/><circle cx="9" cy="11" r="5"/><circle cx="9" cy="11" r="2.6"/><line x1="17" y1="9" x2="25" y2="9"/><line x1="17" y1="12" x2="25" y2="12"/></svg>
    <h3 class="card-title">TOP-Konditionen</h3>
    <p class="card-text">Muster Text Lorem ipsum dolor sit amet, consetetur sadipscing elitr, sed diam nonumy eirmod temporet invidunt ut labore et dolore magna.</p>
  </article>
  <article class="card" style="left:281px">
    <div class="card-visual" role="img" aria-label="Präsentation vor einer großen Projektionswand mit Diagrammen" style="clip-path:polygon(82px 0,153px 0,153px 115px,55px 103px,48px 88px);background:linear-gradient(150deg,#5a49d6,#2b1f8e)"></div>
    <svg class="card-icon" viewBox="0 0 29 22" fill="none" stroke="#fff" stroke-width=".9"><path d="M1 5V1H5M24 1H28V5M28 17V21H24M5 21H1V17"/><text x="14.5" y="15" text-anchor="middle" font-family="Jost, sans-serif" font-size="10" font-weight="300" fill="#fff" stroke="none">1080</text></svg>
    <h3 class="card-title">Full-HD Beamer</h3>
    <p class="card-text">Muster Text Lorem ipsum dolor sit amet, consetetur sadipscing elitr, sed diam nonumy eirmod temporet invidunt ut labore et dolore magna.</p>
  </article>
  <article class="card" style="left:453px">
    <div class="card-visual" role="img" aria-label="Aufgestellte Projektionsleinwand in einem Raum" style="clip-path:polygon(82px 0,153px 0,153px 115px,58px 103px,48px 88px);background:linear-gradient(150deg,#f1f1f3,#cfcfd4)"></div>
    <svg class="card-icon" viewBox="0 0 29 22" fill="none" stroke="#fff" stroke-width=".9"><rect x="2" y="1" width="25" height="15"/><path d="M14.5 16V21M14.5 17L10 21M14.5 17L19 21"/></svg>
    <h3 class="card-title" style="top:33px">Leinwände</h3>
    <p class="card-text">Muster Text Lorem ipsum dolor sit amet, consetetur sadipscing elitr, sed diam nonumy eirmod temporet invidunt ut labore et dolore magna.</p>
  </article>

  <div class="abs contact-art" role="img" aria-label="Illustration zweier Sprechblasen als Symbol für Kontakt"></div>
  <svg class="abs" style="left:108px;top:977px" width="276" height="136" viewBox="0 0 276 136" aria-hidden="true">
    <defs>
      <linearGradient id="contactBand" x1="0" y1="0" x2="1" y2="0">
        <stop offset="0" stop-color="#6c38ab"/>
        <stop offset="1" stop-color="#9b5bcb"/>
      </linearGradient>
    </defs>
    <path d="M4,132 L264,4 Q273,0 273,11 L273,119 Q273,134 258,134 L8,134 Q-1,134 4,132 Z" fill="url(#contactBand)"/>
  </svg>
  <p class="abs contact-kicker">Reservieren oder Buchen</p>
  <h2 class="abs contact-title">Sie haben Interesse an unserer Beamer Vermietung?</h2>
  <p class="abs contact-lead">Dann rufen Sie uns einfach unter einer der unten stehenden Telefonnummern an und fragen Sie nach der Verfügbarkeit des gewünschten Beamers:</p>
  <ul class="abs contact-list">
    <li class="company"><svg viewBox="0 0 5 6"><circle cx="2.5" cy="1.5" r="1.4" fill="#7a44b6"/><path d="M0 6C0 3.5 5 3.5 5 6Z" fill="#7a44b6"/></svg>Marlow Tessendorf GbR</li>
    <li><svg viewBox="0 0 5 6"><rect x=".8" y=".3" width="3.4" height="5.4" rx=".6" fill="none" stroke="#7a44b6" stroke-width=".7"/></svg>04721/ 305829</li>
    <li><svg viewBox="0 0 5 6"><path d="M1 .5L2 .3 2.6 1.8 1.9 2.4Q2.4 3.6 3.3 4.2L3.9 3.6 5 4.3 4.7 5.4Q1.5 5.3.4 1.4Z" fill="#7a44b6"/></svg>0171 / 4820396</li>
  </ul>

  <div class="abs footer-rule"></div>
  <p class="abs footer-copy">© Copyright © 2020 Projektor-Verleih-Raum-Wendbergshof.de – Beamer mieten in Wendbergshof. Alle Rechte vorbehalten.</p>
  <div class="abs footer-links"><span>Impressum</span><span>Datenschutz</span><span class="dot"></span><span class="dot"></span></div>

</div>
</body>
</html>
```